Coastal Learner Bureau business cards

Australian company about to start offering its services. We recruit international students to come to study English, vocational education and postgraduate courses in Australia. We help them find the institution and select the right city they want to come to Australia. We are a young, online oriented and supportive agency. Our clients are between 18 and 35 years old, mainly University students, young professionals or people with work experience. We provide much more information that any other agency offer. We administrate a Facebook group with more than 11.000 members that daily ask questions about general information when coming to Australia, while they are here and even after they leave the country

Target Market(s)

International students from South America, Central America and Europe

Industry/Entity Type

Student

Contact Information for Business Card

Tomas Bilbrea
Managing Director
tomas@kelvarin.com.au
www.kelvoria.com.au
+61 491058264
Melbourne, Australia

Font styles to use
Serif
Sans Serif

Colors

Designer to choose colors to be used in the design.

Requirements
Must have
• Horizontal design
• Standard business card size and shape. If font uses green or yellow colours, they will have to match the ones from the logo
Nice to have
• UPDATE: Use the contents of the green image to design one of the card sides. Use our logo in the background of that side as watermark.
• Passport image, or immigration stamps. A picture of the Yarra River (from Melbourne) would be cool as well.
Should not have
• Non-standard business card size and shape
• Not black as the background colour of any sides as we are not a VIP agency or a hight class service. We are orientes to young people and they like colours, pictures, something attractive.
• Vertical design
• NO YELLOW or BLACK AS THE BACKGROUND COLOUR OF ANY SIDE OF THE BIZ CARD

```html
<!DOCTYPE html>
<html lang="en">
<head>
<meta charset="utf-8">
<title>Coastal Learner Bureau — Business Cards</title>
<link rel="stylesheet" href="https://fonts.googleapis.com/css2?family=Montserrat:wght@700&family=Didact+Gothic&display=swap">
<style>
  :root {
    --backdrop: #8e8d8e;
    --green: #135f44;
    --green-soft: #1b6c4e;
    --yellow: #e2b823;
    --paper: #ffffff;
    --ink: #3b3b3b;
  }
  * { box-sizing: border-box; margin: 0; padding: 0; }
  html, body { width: 1200px; height: 929px; overflow: hidden; }
  body {
    background: var(--backdrop);
    position: relative;
    font-family: "Didact Gothic", "Century Gothic", sans-serif;
  }
  .card {
    position: absolute;
    width: 630px;
    height: 360px;
    overflow: hidden;
  }

  /* Back side */
  .card-back { left: 80px; top: 70px; background: var(--green); }
  .card-back .map-area {
    position: absolute;
    left: 130px; top: 50px;
    width: 370px; height: 230px;
    border-radius: 40% 46% 38% 44%;
    background: radial-gradient(ellipse at center, var(--green-soft) 0%, var(--green) 75%);
  }
  .card-back .brand {
    position: absolute;
    left: 0; right: 0; top: 150px;
    text-align: center;
    font-family: "Montserrat", sans-serif;
    font-weight: 700;
    font-size: 30px;
    color: var(--paper);
    letter-spacing: 0.5px;
  }
  .card-back .tagline {
    position: absolute;
    left: 0; right: 0; bottom: 48px;
    text-align: center;
    font-size: 13px;
    letter-spacing: 1px;
    color: var(--paper);
  }

  /* Front side */
  .card-front { left: 490px; top: 500px; background: var(--paper); }
  .card-front .brand {
    position: absolute;
    left: 40px; top: 70px;
    width: 230px;
    font-family: "Montserrat", sans-serif;
    font-weight: 700;
    font-size: 28px;
    line-height: 1.1;
    color: var(--green);
  }
  .card-front .side-tab {
    position: absolute;
    right: 0; top: 72px;
    width: 10px; height: 44px;
    background: var(--green);
    border-radius: 8px 0 0 8px;
  }
  .identity {
    position: absolute;
    right: 50px; top: 86px;
    text-align: right;
  }
  .identity .name {
    font-family: "Montserrat", sans-serif;
    font-weight: 700;
    font-size: 24px;
    color: var(--green);
    letter-spacing: 0.5px;
  }
  .identity .role {
    font-size: 15px;
    color: var(--ink);
    margin-top: 2px;
  }
  .divider {
    position: absolute;
    left: 40px; top: 172px;
    width: 380px; height: 2px;
    background: var(--green);
  }
  .location {
    position: absolute;
    right: 40px; top: 168px;
    text-align: right;
    font-size: 14px;
    line-height: 1.35;
    color: var(--ink);
  }
  .contacts {
    position: absolute;
    left: 40px; top: 196px;
    list-style: none;
  }
  .contacts li {
    display: flex;
    align-items: center;
    gap: 12px;
    font-size: 15px;
    color: var(--ink);
    height: 24px;
    letter-spacing: 0.3px;
  }
  .contacts svg { width: 13px; height: 13px; flex: none; }
  .band {
    position: absolute;
    bottom: 0; height: 30px;
  }
  .band-green { left: 0; width: 75%; background: var(--green); }
  .band-yellow { right: 0; width: calc(25% - 6px); background: var(--yellow); height: 40px; }
</style>
</head>
<body>

  <section class="card card-back" aria-label="Business card, back">
    <div class="map-area" role="img" aria-label="Faint dotted map of Australia as a background watermark"></div>
    <div class="brand">Coastal Learner Bureau</div>
    <p class="tagline">Hacemos más por ti!</p>
  </section>

  <section class="card card-front" aria-label="Business card, front">
    <div class="brand">Coastal Learner Bureau</div>
    <div class="side-tab"></div>
    <div class="identity">
      <p class="name">TOMAS BILBREA</p>
      <p class="role">Managing Director</p>
    </div>
    <div class="divider"></div>
    <p class="location">Melbourne,<br>Australia</p>
    <ul class="contacts">
      <li>
        <svg viewBox="0 0 14 14" aria-hidden="true"><rect x="3.5" y="1" width="7" height="12" rx="1.2" fill="none" stroke="var(--green)" stroke-width="1.4"/><line x1="6" y1="11" x2="8" y2="11" stroke="var(--green)" stroke-width="1.2"/></svg>
        +61 491058264
      </li>
      <li>
        <svg viewBox="0 0 14 14" aria-hidden="true"><rect x="1" y="3" width="12" height="8.5" fill="var(--green)"/><polyline points="1,3 7,8 13,3" fill="none" stroke="var(--paper)" stroke-width="1.2"/></svg>
        tomas@kelvarin.com.au
      </li>
      <li>
        <svg viewBox="0 0 14 14" aria-hidden="true"><circle cx="5.5" cy="5.5" r="3.8" fill="none" stroke="var(--green)" stroke-width="1.8"/><line x1="8.3" y1="8.3" x2="12.5" y2="12.5" stroke="var(--green)" stroke-width="2"/></svg>
        www.kelvoria.com.au
      </li>
    </ul>
    <div class="band band-green"></div>
    <div class="band band-yellow"></div>
  </section>

</body>
</html>
```